Business Card - high end, modern health care

Hey designers!

We need a double sided business card for the boutique, cutting edge physical therapy rehabilitation centre in Sydney's Northern Beaches.

With the most qualified physios in the area The Harbourview Motion Clinic does what other physiotherapy practices do not, we take our time with our patients giving them longer appointments, better physios and therefor faster results!

We guarantee that the service people receive at THMC will be unparalleled.

Hence we need a business card to reflect our modern, boutique, high end service. The final design needs to reflect that we are in a class of our own yet with the feel of beachside retreat.

Below I have attached our logo in both blue on white and white on blue. The exact colour is;
and the font that we have used in our logo is Tex Gyre Aventador.

I like the idea of the blue as the main colour as it is more eye catching and our signage onto the main road will be in this blue and in the interest of consistency across marketing the blue needs to be a part of the design. However I would appreciate a few designs onto a wooden background as this is a visual theme within the fitout of the practice.

The design needs to be of standard size (91x55mm).

Target Market(s)

We target people who have an end outcome in mind and those who have had poor experiences with other providers and ensure that everyone gets the care that they deserve with a premium service that is tailored to the individuals circumstances. As a premium service, the target market is highly educated, business and tech savvy with the additional target market of elderly people who have self funded their retirement and see value in paying for the best ongoing rehabilitation to maintain independence.

Industry/Entity Type

Physical Therapy

Contact Information for Business Card

Name, designation( Titled Musculoskeletal Physiotherapist... there will also be those in the company that have multiple designations ie 5 or 6 words long), phone number, email, facebook, instagram, address

Font styles to use
Sans Serif

Colors

Designer to choose colors to be used in the design.

Requirements
Must have
• Front - The logo as large as possible, blue or wooden theme, and all of the important details.
• Back - A blank space/lines on which to write appointment times (no "Appointment, date, time" etc.)
Nice to have
• facebook url
• logos for facebook and instagram
• Mini logos for the phone and email?

```html
<!DOCTYPE html>
<html lang="en">
<head>
<meta charset="utf-8">
<title>The Harbourview Motion Clinic – Business Card</title>
<link href="https://fonts.googleapis.com/css2?family=Montserrat:wght@400;500;600;700&display=swap" rel="stylesheet">
<style>
  :root{
    --navy:#0f3470;
    --navy-deep:#0b2a5e;
    --brand:#1452a8;
    --brand-light:#2f6fc4;
    --white:#ffffff;
    --paper:#f4f6f9;
    --line:#3a6fc0;
  }
  *{margin:0;padding:0;box-sizing:border-box}
  html,body{width:800px;height:1200px;overflow:hidden}
  body{
    font-family:"Montserrat",sans-serif;
    background:radial-gradient(ellipse at 50% 40%,#194585 0%,var(--navy) 55%,var(--navy-deep) 100%);
    position:relative;
  }
  .card{
    position:absolute;top:430px;width:360px;height:200px;border-radius:14px;overflow:hidden;
    box-shadow:0 10px 22px rgba(0,0,0,.35);
  }
  .card--front{left:30px;background:linear-gradient(120deg,#1a4c98 0%,var(--brand) 55%,#2060b4 100%)}
  .card--back{left:412px;background:linear-gradient(160deg,var(--white) 0%,var(--paper) 100%);border-bottom:8px solid var(--brand)}

  .wordmark{position:absolute;display:flex;align-items:center;gap:7px}
  .wordmark__dot{width:34px;height:34px;border-radius:50%;flex:none}
  .wordmark__name{font-weight:600;line-height:1.05;text-transform:uppercase}
  .wordmark__name span{display:block}
  .wordmark__name .sub{letter-spacing:.22em}

  .card--front .wordmark{left:22px;top:28px}
  .card--front .wordmark__dot{background:var(--white)}
  .card--front .wordmark__name{color:var(--white);font-size:15px}
  .card--front .wordmark__name .sub{font-size:12px}

  .front-art{
    position:absolute;right:-70px;top:10px;width:210px;height:210px;border-radius:50%;
    background:radial-gradient(circle at 38% 55%,var(--white) 0 38%,var(--brand-light) 39% 100%);
    border:6px solid var(--white);
  }
  .person{position:absolute;left:22px;top:102px;color:var(--white);width:214px}
  .person__name{font-weight:700;font-size:10.5px;letter-spacing:.03em}
  .person__role{font-size:7.5px;margin-top:2px;padding-bottom:6px;border-bottom:1px solid rgba(255,255,255,.8)}
  .contacts{list-style:none;margin-top:6px;font-size:7.2px}
  .contacts li{display:flex;align-items:center;gap:6px;height:15px}
  .contacts svg{width:9px;height:9px;flex:none}
  .social{display:inline-flex;align-items:center;gap:4px;margin-left:14px}
  .social i{width:8px;height:8px;border-radius:50%;background:var(--white);display:inline-block}

  .back-art{
    position:absolute;left:-110px;top:-10px;width:220px;height:220px;border-radius:50%;
    background:radial-gradient(circle at 60% 50%,#3c78c8 0%,var(--brand) 55%,#0d3f8a 100%);
  }
  .card--back .wordmark{left:128px;top:46px}
  .card--back .wordmark__dot{background:var(--brand)}
  .card--back .wordmark__name{color:var(--brand);font-size:14px}
  .card--back .wordmark__name .sub{font-size:11px}
  .note-box{
    position:absolute;left:126px;top:94px;width:196px;height:56px;border:1px solid var(--line);border-radius:7px;
    padding:12px 16px 0;
  }
  .note-box hr{border:none;border-top:1px solid #9bb3d6;margin-bottom:10px}

  .lockup{position:absolute;left:0;right:0;top:800px;display:flex;justify-content:center}
  .lockup .wordmark{position:static;gap:12px}
  .lockup .wordmark__dot{width:54px;height:54px;background:var(--white)}
  .lockup .wordmark__name{color:var(--white);font-size:27px}
  .lockup .wordmark__name .sub{font-size:21px}
</style>
</head>
<body>
  <section class="card card--front">
    <div class="front-art" role="img" aria-label="Large decorative ocean wave graphic"></div>
    <div class="wordmark">
      <span class="wordmark__dot"></span>
      <p class="wordmark__name"><span>The Harbourview</span><span class="sub">Motion Clinic</span></p>
    </div>
    <div class="person">
      <p class="person__name">DANIEL REEVES</p>
      <p class="person__role">Titled Musculoskeletal Physiotherapist</p>
      <ul class="contacts">
        <li>
          <svg viewBox="0 0 10 10"><circle cx="5" cy="5" r="5" fill="#fff"/><path d="M3.2 2.6l1 .1.4 1.1-.6.5a3.6 3.6 0 0 0 1.7 1.7l.5-.6 1.1.4.1 1c-2.5.3-4.5-1.7-4.2-4.2z" fill="#1452a8"/></svg>
          0061 400 123
          <span class="social"><i></i> harbourviewmotionclinic</span>
        </li>
        <li>
          <svg viewBox="0 0 10 10"><circle cx="5" cy="5" r="5" fill="#fff"/><rect x="2.5" y="3.2" width="5" height="3.6" fill="#1452a8"/><path d="M2.5 3.3L5 5.2l2.5-1.9" stroke="#fff" stroke-width=".6" fill="none"/></svg>
          contact@harbourviewmotion.com.au
        </li>
        <li>
          <svg viewBox="0 0 10 10"><circle cx="5" cy="5" r="5" fill="#fff"/><path d="M5 2.2a1.9 1.9 0 0 0-1.9 1.9C3.1 5.5 5 7.9 5 7.9s1.9-2.4 1.9-3.8A1.9 1.9 0 0 0 5 2.2z" fill="#1452a8"/><circle cx="5" cy="4.1" r=".7" fill="#fff"/></svg>
          1820 Pittwater Road, NSW 2100 Australia
        </li>
      </ul>
    </div>
  </section>

  <section class="card card--back">
    <div class="back-art" role="img" aria-label="Large decorative fern frond illustration in blue"></div>
    <div class="wordmark">
      <span class="wordmark__dot"></span>
      <p class="wordmark__name"><span>The Harbourview</span><span class="sub">Motion Clinic</span></p>
    </div>
    <div class="note-box"><hr><hr><hr></div>
  </section>

  <div class="lockup">
    <div class="wordmark">
      <span class="wordmark__dot"></span>
      <p class="wordmark__name"><span>The Harbourview</span><span class="sub">Motion Clinic</span></p>
    </div>
  </div>
</body>
</html>
```